Very visible CoWorking Building Sign overlooking downtown LA and 110 freeway

Our building is drab but very visible and in the best location. We need a great sign for our monolith that overlooks downtown LA and the 100 freeway. We are a new CoWorking business and would like to have a few things we do on the sign: private offices, virtual offices, CoWorking Lounge. Everything we have seen is ho-hum. Can you get us noticed? We need people to know what we do and that we are here but in a creative, professional, unique sign.
Target Market(s)
People who have a business in DTLA, remote workers and those who work from home who need a professional address.
Requirements
Must have
- Our logo (which can be somewhat reimagined) which has our address 2417 on it. The three things we focus on: Private Offices, Virtual Offices, CoWorking Lounge. Incorporate some Navy. Readable from several hundred feet away.
Nice to have
- Mural feel? Something inspirational in this crazy COVID times? Graphics? Color block. I like the idea of decorative but it has to be readable as a building sign. The same with the use of colors. Our colors are grays and navy but with a pop of the chartreuse (we have 2 velvet chartreuse chairs in the space). Helpful to view our website: Harborview2417.com.
Should not have
- Not too graffiti. Keep it professional but unique and wow.

```html
<!DOCTYPE html>
<html lang="en">
<head>
<meta charset="utf-8">
<title>Harborview 2417 – Building Sign</title>
<link rel="stylesheet" href="https://fonts.googleapis.com/css2?family=Red+Hat+Display:wght@500;700;800&family=Montserrat:wght@600&display=swap">
<style>
  :root {
    --navy: #0b3f7f;
    --navy-deep: #17325f;
    --chartreuse: #8cc63f;
    --panel: #f3f4f6;
    --bar: #ffffff;
    --bg-light: #ffffff;
    --bg-gray: #c8c8c8;
  }
  * { margin: 0; padding: 0; box-sizing: border-box; }
  html, body {
    width: 1200px;
    height: 960px;
    overflow: hidden;
  }
  body {
    background: linear-gradient(135deg, var(--bg-light) 0%, #ececec 45%, var(--bg-gray) 100%);
    display: flex;
    align-items: center;
    justify-content: center;
  }
  .building-sign {
    width: 1060px;
    height: 177px;
    display: block;
    filter: drop-shadow(0 6px 14px rgba(0, 0, 0, 0.12));
  }
  .sign-panel { fill: var(--panel); }
  .sign-navy { fill: var(--navy); }
  .brand-name {
    font-family: "Red Hat Display", sans-serif;
    font-weight: 500;
    fill: var(--navy-deep);
  }
  .site-address {
    font-family: "Montserrat", sans-serif;
    font-weight: 600;
    fill: var(--navy);
    letter-spacing: 4px;
  }
  .service-bar { fill: var(--bar); }
  .service-underline { fill: var(--chartreuse); }
  .service-tab { fill: var(--chartreuse); }
  .service-tick {
    fill: none;
    stroke: var(--bar);
    stroke-width: 5;
    stroke-linecap: round;
    stroke-linejoin: round;
  }
  .service-label {
    font-family: "Red Hat Display", sans-serif;
    font-weight: 700;
    fill: var(--navy);
    font-size: 46px;
  }
</style>
</head>
<body>
  <svg class="building-sign" viewBox="0 0 1908 318" xmlns="http://www.w3.org/2000/svg" aria-label="Harborview 2417 coworking building sign">
    <rect class="sign-panel" x="0" y="0" width="1908" height="318"/>
    <path class="sign-navy" d="M1908 14 H1095 C1045 14 1022 36 1000 78 L888 284 C872 304 850 307 810 307 H0 V318 H1908 Z"/>

    <text class="site-address" x="480" y="84" font-size="26">www.harborview2417.com</text>
    <text class="brand-name" x="100" y="268" font-size="92" textLength="760" lengthAdjust="spacingAndGlyphs">HARBORVIEW 2417</text>

    <g class="service-item" transform="translate(1100 57)">
      <rect class="service-bar" x="0" y="0" width="682" height="49" rx="4"/>
      <rect class="service-underline" x="100" y="46" width="582" height="3"/>
      <polygon class="service-tab" points="0,0 76,0 104,49 0,49"/>
      <polyline class="service-tick" points="28,25 38,36 56,12"/>
      <text class="service-label" x="120" y="42">PRIVATE OFFICES</text>
    </g>
    <g class="service-item" transform="translate(1100 138)">
      <rect class="service-bar" x="0" y="0" width="682" height="49" rx="4"/>
      <rect class="service-underline" x="100" y="46" width="582" height="3"/>
      <polygon class="service-tab" points="0,0 76,0 104,49 0,49"/>
      <polyline class="service-tick" points="28,25 38,36 56,12"/>
      <text class="service-label" x="122" y="42">VIRTUAL OFFICES</text>
    </g>
    <g class="service-item" transform="translate(1100 219)">
      <rect class="service-bar" x="0" y="0" width="682" height="49" rx="4"/>
      <rect class="service-underline" x="100" y="46" width="582" height="3"/>
      <polygon class="service-tab" points="0,0 76,0 104,49 0,49"/>
      <polyline class="service-tick" points="28,25 38,36 56,12"/>
      <text class="service-label" x="120" y="42">COWORKING LOUNGE</text>
    </g>
  </svg>
</body>
</html>
```